Sands: A Lantern - Unbroken (format 130 x 190mm)

Book cover design for an Islamic title.
I need open Indesign or Photoshop files so I can adjust the sizes etc.!
(format 130 x 190mm)
With the following blurb:
“It was a Friday when the earth unexpectedly felt a foot moving on it. A feeling that was completely foreign to her…”

And then you find yourself in the middle of a journey through the history of humanity and at the same time the history of Islam:

• How did humanity develop and who were the Arabs?
• Also, who was this one Arab who was destined to place the fate of the world on his shoulders ﷺ?
• How does the message delivered by Muḥammad ﷺ affect the entire cosmos – visible and invisible?
• What is the Ka'bah all about?
• What role did the most important person in the life of the best person on earth ﷺ play in the message he had to proclaim?

In short: "These few pages are intended to show what distinguishes the final message and what makes it so incomparable, a message 'unparalleled'..."

(format 130 x 190mm)

Front cover:
A message
Unparalleled
from
Dr. Ḥāmid Ṭāriq Qurašī
Translated by
Petra Kühnert
Our logo

Back cover:

Our Logo, ISBN: 978-3-952284-36-9
Website: tkpresse. de
Shop: lesehain-shop.de

Islamic Literature

• No Pictures of Human Beings.

```html
<!DOCTYPE html>
<html lang="en">
<head>
<meta charset="utf-8">
<title>A Lantern Unbroken – Front Cover</title>
<link rel="stylesheet" href="https://fonts.googleapis.com/css2?family=Aref+Ruqaa:wght@400;700&family=EB+Garamond:ital,wght@0,400;0,600;1,400&display=swap">
<style>
  :root {
    --backdrop: #262626;
    --cover: #000000;
    --gold: #e3b25a;
    --gold-light: #f4d68f;
    --gold-deep: #c9923c;
    --gold-glow: rgba(255, 214, 140, 0.45);
    --ink-white: #ffffff;
    --scene-amber: #c98a45;
    --scene-brown: #5a3318;
    --scene-deep: #1e0f07;
  }
  * { margin: 0; padding: 0; box-sizing: border-box; }
  html, body {
    width: 1200px; height: 1200px; overflow: hidden;
    background: var(--backdrop);
  }
  .cover {
    position: absolute; left: 207px; top: 25px;
    width: 786px; height: 1149px;
    background: var(--cover);
    overflow: hidden;
  }
  .cover-art {
    position: absolute; left: 82px; top: 279px;
    width: 608px; height: 776px;
    background:
      radial-gradient(ellipse 22% 38% at 50% 36%, #fff3d6 0%, #f0cf8e 35%, rgba(201,138,69,0) 100%),
      radial-gradient(ellipse 60% 60% at 50% 55%, var(--scene-amber) 0%, var(--scene-brown) 45%, var(--scene-deep) 75%, rgba(0,0,0,0) 100%);
    -webkit-mask-image: radial-gradient(ellipse 70% 75% at 50% 50%, #000 55%, transparent 100%);
    mask-image: radial-gradient(ellipse 70% 75% at 50% 50%, #000 55%, transparent 100%);
  }
  .line {
    position: absolute; left: 0; width: 100%;
    text-align: center; white-space: nowrap;
  }
  .title-small {
    top: 38px;
    font-family: "Aref Ruqaa", serif; font-size: 56px; line-height: 1;
    color: var(--ink-white);
  }
  .title-main {
    top: 100px;
    font-family: "Aref Ruqaa", serif; font-weight: 400;
    font-size: 150px; line-height: 1;
    color: var(--gold);
    filter: drop-shadow(0 0 10px var(--gold-glow));
  }
  .title-main span {
    background: linear-gradient(180deg, var(--gold-light), var(--gold) 60%, var(--gold-deep));
    -webkit-background-clip: text; background-clip: text;
    -webkit-text-fill-color: transparent;
  }
  .byline-from {
    top: 252px;
    font-family: "EB Garamond", serif; font-style: italic;
    font-size: 27px; line-height: 1.2; color: var(--ink-white);
  }
  .byline-author {
    top: 290px;
    font-family: "EB Garamond", serif; font-weight: 600;
    font-size: 25px; line-height: 1.2; color: var(--ink-white);
  }
  .publisher {
    position: absolute; left: 0; top: 1044px; width: 100%;
    display: flex; align-items: center; justify-content: center; gap: 8px;
    font-family: "EB Garamond", serif; font-size: 15px; line-height: 1;
    color: var(--ink-white);
  }
  .publisher-mark {
    width: 11px; height: 11px; border: 1.5px solid var(--ink-white);
  }
  .translator {
    top: 1080px;
    font-family: "EB Garamond", serif; font-size: 26px; line-height: 1.2;
    color: var(--ink-white);
  }
  .translator em { font-style: italic; }
</style>
</head>
<body>
  <main class="cover">
    <div class="cover-art" role="img" aria-label="Painterly scene in warm amber light: a glowing arched doorway in a dim hall, fading into black"></div>
    <p class="line title-small">A Lantern</p>
    <h1 class="line title-main"><span>Unbroken</span></h1>
    <p class="line byline-from">from</p>
    <p class="line byline-author">Dr. Ḥāmid Ṭāriq Qurašī</p>
    <div class="publisher"><span class="publisher-mark"></span><span>Tintenkreis Presse</span></div>
    <p class="line translator"><em>Translated by</em> Petra Kühnert</p>
  </main>
</body>
</html>
```